Orvane Mechanical - Letterhead

We are a plumbing and hvac company based in Calgary. This letterhead will be on our quotes, invoices, preventative maintenance proposals etc.

```html
<!DOCTYPE html>
<html lang="en">
<head>
<meta charset="utf-8">
<title>Orvane Mechanical – Letterhead</title>
<link href="https://fonts.googleapis.com/css2?family=Open+Sans:wght@400;700&family=Roboto:wght@400&display=swap" rel="stylesheet">
<style>
  :root {
    --backdrop: #dedede;
    --paper: #fafafa;
    --brand-orange: #e8592a;
    --brand-blue: #1f6fb5;
    --ink: #4a4a4a;
    --ink-soft: #3a3a3a;
    --mark-tint: #f6ecea;
    --signature-tint: #ececec;
  }
  * { margin: 0; padding: 0; box-sizing: border-box; }
  html, body {
    width: 1200px; height: 800px; overflow: hidden;
    background: var(--backdrop);
  }
  .canvas { position: relative; width: 1200px; height: 800px; }

  .letterhead {
    position: absolute; top: 111px;
    width: 412px; height: 574px;
    background: var(--paper);
    overflow: hidden;
    font-family: "Open Sans", sans-serif;
    color: var(--ink);
  }
  .letterhead--first { left: 165px; }
  .letterhead--second { left: 613px; }

  .watermark {
    position: absolute; right: -22px; top: 386px;
    width: 158px; height: 158px; border-radius: 50%;
    background: var(--mark-tint);
    z-index: 0;
  }

  .brand {
    position: absolute; left: 37px; top: 52px;
    display: flex; align-items: center; gap: 6px;
    z-index: 1;
  }
  .brand__dot {
    width: 14px; height: 14px; border-radius: 50%;
    background: var(--brand-orange);
  }
  .brand__name {
    font-family: "Open Sans", sans-serif;
    font-weight: 700; font-size: 11px; letter-spacing: 0.6px;
    color: var(--brand-blue);
    text-transform: uppercase;
  }

  .contact {
    position: absolute; left: 275px; top: 40px;
    border-left: 1.2px solid var(--brand-blue);
    padding-left: 11px;
    font-family: "Roboto", sans-serif;
    font-style: normal;
    font-size: 7.2px; line-height: 9.2px;
    color: var(--ink-soft);
    z-index: 1;
  }
  .contact__address { margin-bottom: 2px; }
  .contact__row { display: flex; align-items: center; gap: 3px; }
  .contact__icon { width: 6px; height: 6px; flex: none; }

  .letter {
    position: absolute; left: 37px; top: 134px; width: 338px;
    font-size: 7.4px; line-height: 11.1px;
    z-index: 1;
  }
  .letter__greeting { margin-bottom: 11px; }
  .letter__para {
    text-align: justify; text-align-last: left;
    margin-bottom: 11px;
  }
  .letter__closing { margin-bottom: 10px; }

  .signature {
    width: 50px; height: 44px;
    background: var(--signature-tint);
    border-radius: 3px;
  }

  .footer-band {
    position: absolute; left: 0; right: 0; bottom: 0; height: 12px;
    display: flex; gap: 3px;
    z-index: 1;
  }
  .footer-band__orange { width: 123px; background: var(--brand-orange); }
  .footer-band__blue { flex: 1; background: var(--brand-blue); }
</style>
</head>
<body>
<main class="canvas">

  <article class="letterhead letterhead--first">
    <div class="watermark"></div>
    <header class="brand">
      <span class="brand__dot"></span>
      <span class="brand__name">Orvane Mechanical</span>
    </header>
    <address class="contact">
      <div class="contact__address">2150 Macleod Trail SE,<br>Suite 310 Calgary.</div>
      <div class="contact__row">
        <svg class="contact__icon" viewBox="0 0 10 10"><path d="M1 4 Q5 0 9 4 L8 5 L6.5 4 V3 H3.5 V4 L2 5 Z M2.5 6 H7.5 L8 9 H2 Z" fill="var(--brand-orange)"/></svg>
        <span>403.555.0148</span>
      </div>
      <div class="contact__row">
        <svg class="contact__icon" viewBox="0 0 10 10"><rect x="0.5" y="2" width="9" height="6.5" fill="var(--brand-orange)"/><path d="M0.5 2 L5 6 L9.5 2" stroke="#fff" stroke-width="0.9" fill="none"/></svg>
        <span>info@orvanemech.ca</span>
      </div>
      <div class="contact__row">
        <svg class="contact__icon" viewBox="0 0 10 10"><circle cx="5" cy="5" r="4.5" fill="var(--brand-orange)"/><path d="M3 2.5 Q5 4 3.5 6 M6.5 4 Q7.5 6 6 8" stroke="#fff" stroke-width="0.9" fill="none"/></svg>
        <span>www.orvanemech.ca</span>
      </div>
    </address>
    <section class="letter">
      <p class="letter__greeting">Dear customer,</p>
      <p class="letter__para">Lorem ipsum dolor sit amet, consectetur adipisicing elit, sed do eiusmod tempor incididunt ut labore et dolore magna aliqua. Ut enim ad minim veniam, quis nostrud exercitation ullamco laboris nisi ut aliquip ex ea commodo consequat. Duis aute irure dolor in reprehenderit in voluptate velit esse cillum dolore eu fugiat nulla pariatur. Excepteur sint occaecat cupidatat non proident, sunt in culpa qui officia deserunt mollit anim id est laborum.</p>
      <p class="letter__para">Lorem ipsum dolor sit amet, consectetur adipisicing elit, sed do eiusmod tempor incididunt ut labore et dolore magna aliqua. Ut enim ad minim veniam, quis nostrud exercitation ullamco laboris nisi ut aliquip ex ea commodo consequat. Duis aute irure dolor in reprehenderit in voluptate velit esse cillum dolore eu fugiat nulla pariatur. Excepteur sint occaecat cupidatat non proident, sunt in culpa qui officia deserunt mollit anim id est laborum.</p>
      <p class="letter__para">Lorem ipsum dolor sit amet, consectetur adipisicing elit, sed do eiusmod tempor incididunt ut labore et dolore magna aliqua. Ut enim ad minim veniam, quis nostrud exercitation ullamco laboris nisi ut aliquip ex ea commodo consequat. Duis aute irure dolor in reprehenderit in voluptate velit esse cillum dolore eu fugiat nulla pariatur. Excepteur sint occaecat cupidatat non proident, sunt in culpa qui officia deserunt mollit anim id est laborum.</p>
      <p class="letter__para">Lorem ipsum dolor sit amet, consectetur adipisicing elit, sed do eiusmod tempor incididunt ut labore et dolore magna aliqua. Ut enim ad minim veniam, quis nostrud exercitation ullamco laboris nisi ut aliquip ex ea commodo consequat. Duis aute irure dolor in reprehenderit.</p>
      <p class="letter__closing">Yours Sincerely,</p>
      <div class="signature" role="img" aria-label="Handwritten signature of the sender"></div>
    </section>
    <footer class="footer-band">
      <span class="footer-band__orange"></span>
      <span class="footer-band__blue"></span>
    </footer>
  </article>

  <article class="letterhead letterhead--second">
    <div class="watermark"></div>
    <header class="brand">
      <span class="brand__dot"></span>
      <span class="brand__name">Orvane Mechanical</span>
    </header>
    <address class="contact">
      <div class="contact__address">2150 Macleod Trail SE,<br>Suite 310 Calgary.</div>
      <div class="contact__row">
        <svg class="contact__icon" viewBox="0 0 10 10"><path d="M1 4 Q5 0 9 4 L8 5 L6.5 4 V3 H3.5 V4 L2 5 Z M2.5 6 H7.5 L8 9 H2 Z" fill="var(--brand-orange)"/></svg>
        <span>403.555.0148</span>
      </div>
      <div class="contact__row">
        <svg class="contact__icon" viewBox="0 0 10 10"><rect x="0.5" y="2" width="9" height="6.5" fill="var(--brand-orange)"/><path d="M0.5 2 L5 6 L9.5 2" stroke="#fff" stroke-width="0.9" fill="none"/></svg>
        <span>info@orvanemech.ca</span>
      </div>
      <div class="contact__row">
        <svg class="contact__icon" viewBox="0 0 10 10"><circle cx="5" cy="5" r="4.5" fill="var(--brand-orange)"/><path d="M3 2.5 Q5 4 3.5 6 M6.5 4 Q7.5 6 6 8" stroke="#fff" stroke-width="0.9" fill="none"/></svg>
        <span>www.orvanemech.ca</span>
      </div>
    </address>
    <section class="letter">
      <p class="letter__greeting">Dear customer,</p>
      <p class="letter__para">Lorem ipsum dolor sit amet, consectetur adipisicing elit, sed do eiusmod tempor incididunt ut labore et dolore magna aliqua. Ut enim ad minim veniam, quis nostrud exercitation ullamco laboris nisi ut aliquip ex ea commodo consequat. Duis aute irure dolor in reprehenderit in voluptate velit esse cillum dolore eu fugiat nulla pariatur. Excepteur sint occaecat cupidatat non proident, sunt in culpa qui officia deserunt mollit anim id est laborum.</p>
      <p class="letter__para">Lorem ipsum dolor sit amet, consectetur adipisicing elit, sed do eiusmod tempor incididunt ut labore et dolore magna aliqua. Ut enim ad minim veniam, quis nostrud exercitation ullamco laboris nisi ut aliquip ex ea commodo consequat. Duis aute irure dolor in reprehenderit in voluptate velit esse cillum dolore eu fugiat nulla pariatur. Excepteur sint occaecat cupidatat non proident, sunt in culpa qui officia deserunt mollit anim id est laborum.</p>
      <p class="letter__para">Lorem ipsum dolor sit amet, consectetur adipisicing elit, sed do eiusmod tempor incididunt ut labore et dolore magna aliqua. Ut enim ad minim veniam, quis nostrud exercitation ullamco laboris nisi ut aliquip ex ea commodo consequat. Duis aute irure dolor in reprehenderit in voluptate velit esse cillum dolore eu fugiat nulla pariatur. Excepteur sint occaecat cupidatat non proident, sunt in culpa qui officia deserunt mollit anim id est laborum.</p>
      <p class="letter__para">Lorem ipsum dolor sit amet, consectetur adipisicing elit, sed do eiusmod tempor incididunt ut labore et dolore magna aliqua. Ut enim ad minim veniam, quis nostrud exercitation ullamco laboris nisi ut aliquip ex ea commodo consequat. Duis aute irure dolor in reprehenderit.</p>
      <p class="letter__closing">Yours Sincerely,</p>
      <div class="signature" role="img" aria-label="Handwritten signature of the sender"></div>
    </section>
    <footer class="footer-band">
      <span class="footer-band__orange"></span>
      <span class="footer-band__blue"></span>
    </footer>
  </article>

</main>
</body>
</html>
```